Business card for my new company (Accounting firm)

I need a business card for my new business Brightwell Advisory and Ledger SA. Our services are accounting, tax, audit and financial management. Our customers are small companies, start-ups and new companies. The final design has to show financial security, trust and growth. Please find our logo attached to the business card. Text for the business card: Brightwell Advisory and Ledger SA Tomas Varenholt Director and Founder Certified Accountant Tel. 022 418 57 34 tv@clairevalconseil.ch www.clairevalconseil.ch Rue des Vergières 27 1201 Geneva
Target Market(s)
Our customers are small companies, start-ups and new companies.
Industry/Entity Type
Finance And Accounting
Contact Information for Business Card
Claireval Conseil et Comptes SA
Tomas Varenholt
Directeur et Fondateur
Expert-comptable diplômé
Tél. 022 418 57 34
tv@clairevalconseil.ch
www.clairevalconseil.ch
Rue des Vergières 27
1201 Genève

```html
<!DOCTYPE html>
<html lang="fr">
<head>
<meta charset="utf-8">
<title>Claireval Conseil et Comptes SA – Carte de visite</title>
<link rel="stylesheet" href="https://fonts.googleapis.com/css2?family=Roboto:wght@400;500;700&display=swap">
<style>
  :root {
    --backdrop: #2a2a2c;
    --white: #ffffff;
    --ink: #3b3b3d;
    --blue-light: #2faee2;
    --blue-mid: #1f8ac9;
    --blue-deep: #176492;
    --back-blue: #1a6594;
    --rule: rgba(255,255,255,0.85);
  }
  * { box-sizing: border-box; margin: 0; padding: 0; }
  html, body {
    width: 1200px; height: 960px; overflow: hidden;
    background: var(--backdrop);
    font-family: "Roboto", Arial, sans-serif;
  }
  .canvas {
    position: relative; width: 1200px; height: 960px;
    display: flex; flex-direction: column; align-items: center;
    justify-content: center; gap: 56px;
  }
  .card {
    width: 720px; height: 411px; position: relative; overflow: hidden;
    box-shadow: 0 10px 28px rgba(0,0,0,0.45);
  }

  /* Back side */
  .card-back {
    background: var(--back-blue);
    display: flex; flex-direction: column; align-items: center; justify-content: center;
    gap: 22px; color: var(--white);
  }
  .back-brand {
    display: flex; align-items: center; gap: 14px;
    font-weight: 500; font-size: 46px; letter-spacing: 4px; color: var(--white);
  }
  .brand-dot { width: 18px; height: 18px; border-radius: 50%; background: var(--blue-light); }
  .back-web { font-size: 20px; letter-spacing: 3px; font-weight: 400; }

  /* Front side */
  .card-front { display: flex; background: var(--white); }
  .front-logo {
    width: 46%; display: flex; align-items: center; justify-content: center; gap: 12px;
  }
  .front-brand {
    font-weight: 500; font-size: 38px; letter-spacing: 3px; color: var(--ink);
  }
  .front-brand-dot { width: 16px; height: 16px; background: var(--blue-mid); }
  .front-info { flex: 1; display: flex; flex-direction: column; color: var(--white); }
  .band { flex: 1; padding: 0 28px; display: flex; flex-direction: column; justify-content: center; }
  .band + .band { border-top: 2px solid var(--rule); }
  .band-person { background: var(--blue-light); }
  .band-address { background: var(--blue-deep); font-size: 17px; line-height: 1.3; }
  .band-contact { background: var(--blue-mid); font-size: 17px; line-height: 1.35; }
  .person-name { font-weight: 700; font-size: 25px; margin-bottom: 2px; }
  .person-role { font-size: 17px; line-height: 1.25; }
  .contact-line { display: flex; align-items: center; gap: 10px; }
  .contact-line svg { width: 16px; height: 16px; flex: none; fill: var(--white); }
</style>
</head>
<body>
<main class="canvas">
  <section class="card card-back" aria-label="Verso de la carte">
    <div class="back-brand"><span class="brand-dot"></span>CLAIREVAL</div>
    <p class="back-web">clairevalconseil.ch</p>
  </section>

  <section class="card card-front" aria-label="Recto de la carte">
    <div class="front-logo">
      <span class="front-brand-dot"></span>
      <span class="front-brand">CLAIREVAL</span>
    </div>
    <div class="front-info">
      <div class="band band-person">
        <p class="person-name">Tomas Varenholt</p>
        <p class="person-role">Directeur et Fondateur</p>
        <p class="person-role">Expert-comptable diplômé</p>
      </div>
      <div class="band band-address">
        <p>Claireval Conseil et Comptes SA</p>
        <p>Rue des Vergières 27</p>
        <p>1201 Genève</p>
      </div>
      <div class="band band-contact">
        <p class="contact-line">
          <svg viewBox="0 0 16 16" aria-hidden="true"><path d="M3.5 1.5l2.3 0 1 3.2-1.6 1.2c.8 1.7 2.2 3.1 3.9 3.9l1.2-1.6 3.2 1v2.3c0 .8-.7 1.5-1.5 1.5C6.6 13 3 9.4 2 3c0-.8.7-1.5 1.5-1.5z"/></svg>
          022 418 57 34
        </p>
        <p class="contact-line">
          <svg viewBox="0 0 16 16" aria-hidden="true"><path d="M1 3h14v10H1z M1.8 3.8L8 8.6l6.2-4.8" stroke="#1f8ac9" stroke-width="1.2"/></svg>
          tv@clairevalconseil.ch
        </p>
        <p class="contact-line">
          <svg viewBox="0 0 16 16" aria-hidden="true"><circle cx="8" cy="8" r="7"/><path d="M1 8h14M8 1c-2.5 2-2.5 12 0 14M8 1c2.5 2 2.5 12 0 14" stroke="#1f8ac9" stroke-width="1" fill="none"/></svg>
          www.clairevalconseil.ch
        </p>
      </div>
    </div>
  </section>
</main>
</body>
</html>
```